Business card

I need a business card design for my consulting company in animal welfare for livestock. I like clean, crisp, simple.

One I imagined was double-sided:
side1: just my name and contact information
side2: silhouette of farm animals. Could be 3 (pig, cow, chicken) or all the species (pig, cow, chicken, duck, sheep, rabbit, etc) that continue the length of the card. I have attached an image of a silhouette style.

But, I am open to any concept.

```html
<!DOCTYPE html>
<html lang="en">
<head>
<meta charset="utf-8">
<title>Humane Practice for Livestock Operations – Business Card</title>
<link rel="stylesheet" href="https://fonts.googleapis.com/css2?family=Fira+Sans:wght@500&family=Inter:wght@200&display=swap">
<style>
  :root {
    --paper: #ffffff;
    --title-green: #4ed24a;
    --contact-teal: #3db8c2;
    --tone-blue: #3a4fd4;
    --tone-teal: #7de0c6;
    --tone-sky: #78dcf6;
    --tone-green: #66f03e;
    --tone-lime: #c2f23e;
    --herd-green: #84cc3a;
    --herd-teal: #45b7c0;
    --herd-blue: #48b8f0;
  }
  html, body {
    margin: 0;
    padding: 0;
    overflow: hidden;
    background: var(--paper);
  }
  .card {
    position: relative;
    width: 1200px;
    height: 741px;
    background: var(--paper);
    overflow: hidden;
  }
  .corner-art {
    position: absolute;
  }
  .corner-art--top-left {
    left: 0;
    top: 0;
    width: 192px;
    height: 373px;
    background: linear-gradient(165deg, var(--tone-green) 0%, var(--tone-teal) 35%, var(--tone-lime) 60%, var(--tone-green) 80%, var(--tone-blue) 100%);
    opacity: .85;
  }
  .corner-art--bottom-right {
    left: 973px;
    top: 407px;
    width: 227px;
    height: 334px;
    background: linear-gradient(170deg, var(--tone-blue) 0%, var(--tone-teal) 35%, var(--tone-sky) 55%, var(--tone-teal) 70%, var(--tone-lime) 100%);
    opacity: .85;
  }

  .company {
    position: absolute;
    left: 222px;
    top: 110px;
    margin: 0;
    font-family: "Fira Sans", sans-serif;
    font-weight: 500;
    font-size: 74px;
    line-height: 78px;
    letter-spacing: 1px;
    color: var(--title-green);
  }
  .contact {
    position: absolute;
    left: 222px;
    top: 305px;
    font-family: "Inter", sans-serif;
    font-weight: 200;
    color: var(--contact-teal);
  }
  .contact__name {
    margin: 0;
    font-size: 66px;
    line-height: 74px;
    letter-spacing: -0.5px;
  }
  .contact__line {
    margin: 0;
    font-size: 43px;
    line-height: 48px;
  }
  .herd {
    position: absolute;
    left: 68px;
    top: 505px;
    width: 240px;
    height: 208px;
    border-radius: 40px 60px 30px 50px;
    background: linear-gradient(160deg, var(--herd-green) 0%, var(--herd-green) 40%, var(--herd-teal) 70%, var(--herd-blue) 100%);
  }
</style>
</head>
<body>
  <div class="card">
    <div class="corner-art corner-art--top-left" role="img" aria-label="Overlapping translucent coloured rectangles in green, teal, lime and blue"></div>
    <div class="corner-art corner-art--bottom-right" role="img" aria-label="Overlapping translucent coloured rectangles in blue, teal, sky and lime"></div>

    <h1 class="company">Humane Practice for<br>Livestock Operations</h1>

    <div class="contact">
      <p class="contact__name">Mara Lindqvist</p>
      <p class="contact__line">Email: mara.lindqvist@mailbox.com</p>
      <p class="contact__line">Tel: +1 604 555 0172</p>
    </div>

    <div class="herd" role="img" aria-label="Overlapping silhouettes of a cow, pig, chicken and rabbit in green, teal and blue"></div>
  </div>
</body>
</html>
```